Homepage for the brisk-find Web Application

At the end of this text, you will find a link to a website that is under construction for a webApp that I intend to launch soon. The contest goal is for you to make redesign the homepage in a nice, fresh, modern Style. Only design, no coding necessary. It needs to have a responsive version for small screens like smart phones. Attached is the text for it, and some images that you may use. You are welcome to find or create additional supporting images. You can use PixTrove.example or similar service to find new images as long as I can purchase the non-exclusive use rights for the images at similar prices. The contest is just for the home page. However, the winner, if I like the work and we can agree on a fair price, could be contracted on a one-on-one basis to do the rest of the site. You are welcome to suggest minor changes like font sizes and minor variations on the Header banner, but that banner is consistent with the user interface of the application therefore should not change too much. The information should flow somewhat continually without much use of side bars or things like that.
https://www.brisk-find.example
Sincerely,
Marco D. Ferral

```html
<!DOCTYPE html>
<html lang="en">
<head>
<meta charset="utf-8">
<title>Brisk Find – Find any document or item instantly</title>
<link href="https://fonts.googleapis.com/css2?family=Arimo:wght@400;700&display=swap" rel="stylesheet">
<style>
:root{
  --blue:#2f7bc0;
  --blue-dark:#1565a8;
  --title-blue:#1a5fa6;
  --orange:#f0643c;
  --orange-footer:#ef6238;
  --footer-bar:#a8240c;
  --grey-bg:#f5f5f5;
  --white:#ffffff;
  --text:#222222;
  --text-soft:#444444;
  --teal:#3bbfcc;
  --teal-light:#bfeef2;
}
*{margin:0;padding:0;box-sizing:border-box}
html,body{width:1200px;height:3750px;overflow:hidden}
body{position:relative;font-family:"Arimo",Arial,sans-serif;color:var(--text);background:var(--white)}
.abs{position:absolute}
.band{position:absolute;left:0;width:1200px}

/* header */
.header-top{top:0;height:74px;background:var(--blue)}
.brand{left:150px;top:18px;display:flex;align-items:center;gap:8px;color:var(--white);font-size:24px}
.brand-dot{width:32px;height:32px;border-radius:50%;background:var(--white)}
.login-field{top:27px;width:153px;height:20px;border-radius:10px;background:var(--orange);color:#ffe1d6;font-size:8px;padding:6px 10px}
.login-btn{left:974px;top:25px;width:74px;height:22px;border-radius:11px;background:var(--orange);color:var(--white);font-size:10px;text-align:center;line-height:22px}
.nav{top:74px;height:37px;background:var(--blue-dark)}
.nav a{position:absolute;top:12px;color:var(--white);font-size:12px;text-decoration:none;transform:translateX(-50%)}

/* hero */
.hero{top:111px;height:748px;background:var(--grey-bg)}
.hero-title{top:155px;width:1200px;text-align:center;color:var(--orange);font-size:24px;font-weight:700}
.illus{border-radius:18px}
.hero-illus{left:400px;top:211px;width:394px;height:371px;background:radial-gradient(ellipse at 50% 55%,#5fd0db 0%,#2aa9b8 55%,var(--grey-bg) 72%)}
.hero-copy{left:180px;top:646px;width:840px;text-align:center;font-size:15px;line-height:22.5px}
.hero-note{top:756px;width:1200px;text-align:center;font-size:15px}
.cta{left:478px;top:798px;width:241px;height:33px;border-radius:17px;background:var(--orange);color:var(--white);font-size:11px;font-weight:700;text-align:center;line-height:33px}

/* why */
.section-title{width:1200px;text-align:center;font-size:18px;font-weight:700;color:var(--title-blue)}
.section-title span{color:var(--orange)}
.why-item{font-size:11.5px;line-height:15.5px;color:var(--text)}

/* storage */
.storage{top:1270px;height:1447px;background:var(--grey-bg)}
.sub-title{font-size:15px;color:var(--title-blue)}
.body-copy{font-size:11.5px;line-height:18px;color:var(--text)}
.body-copy p+p{margin-top:18px}
.phone-illus{left:233px;top:1354px;width:247px;height:342px;background:linear-gradient(160deg,#7fdbe4,#2aa9b8 60%,#bfeef2)}
.big-phone{left:459px;top:1973px;width:291px;height:684px;border-radius:40px;background:linear-gradient(170deg,#8ae0e8,#37b6c4 55%,#9fe2ea)}
.item-label{font-size:12px;color:var(--orange);line-height:15px}
.item-text{font-size:8.5px;line-height:15.5px;color:var(--text-soft)}
.left-item{text-align:right;width:200px}
.right-item{width:220px}

/* alternative */
.alt-copy{left:280px;top:2868px;width:400px;text-align:right;font-size:12px;line-height:18px}
.alt-illus{left:721px;top:2752px;width:189px;height:284px;background:linear-gradient(160deg,#8ae0e8,#2aa9b8 60%,#f3f3f3)}

/* testimonials */
.testi{top:3072px;height:364px;background:var(--grey-bg)}
.card{top:3178px;width:426px;height:185px;background:var(--white);border-radius:10px;box-shadow:0 3px 10px rgba(0,0,0,.12)}
.quote-mark{position:absolute;left:28px;top:16px;width:96px;height:70px}
.card-name{position:absolute;top:30px;width:100%;text-align:center;color:var(--orange);font-size:15px}
.card-text{position:absolute;left:20px;top:78px;width:386px;text-align:center;font-size:8.5px;line-height:15px;color:var(--text-soft)}
.avatar{top:3146px;width:68px;height:68px;border-radius:50%;border:2px solid var(--orange);background:linear-gradient(160deg,#e8dcd6,#b9a49a)}
.dot{top:3394px;width:13px;height:13px;border-radius:50%;background:#3fb6ee}
.dot.active{top:3392px;width:17px;height:17px;background:var(--orange)}

/* footer */
.footer{top:3436px;height:299px;background:var(--orange-footer);color:var(--white)}
.footer-bar{top:3735px;height:15px;background:var(--footer-bar);color:#f6d3c8;font-size:8px;text-align:center;line-height:15px}
.foot-title{font-size:18px;font-weight:700;color:var(--white)}
.foot-text{font-size:10px;line-height:16px;color:var(--white)}
.foot-links a{display:block;color:var(--white);font-size:10.5px;text-decoration:none;margin-bottom:12px;font-weight:700}
.social{width:26px;height:26px;border-radius:50%;background:var(--white)}
</style>
</head>
<body>

<!-- header -->
<div class="band header-top"></div>
<div class="abs brand"><span class="brand-dot"></span>Brisk Find</div>
<div class="abs login-field" style="left:643px">UserName</div>
<div class="abs login-field" style="left:810px">Password</div>
<div class="abs login-btn">Log in</div>
<nav class="band nav">
  <a href="#" style="left:281px">About</a>
  <a href="#" style="left:366px">Pricing</a>
  <a href="#" style="left:446px">Blog</a>
  <a href="#" style="left:523px">FAQs</a>
  <a href="#" style="left:607px">Suppor</a>
  <a href="#" style="left:699px">Reviews</a>
  <a href="#" style="left:801px">Contact Us</a>
  <a href="#" style="left:907px">Free-Trail</a>
</nav>

<!-- hero -->
<section class="band hero"></section>
<h1 class="abs hero-title">Find any document or item instantly!</h1>
<div class="abs illus hero-illus" role="img" aria-label="Illustration of a laptop whose screen opens into filing drawers, with a man holding an orange folder"></div>
<p class="abs hero-copy">Brisk-Find is a system that allows you to quickly search for the location of every item that you store or file. It is an essential tool for keeping track of paper documents or any other kind of physical item. You’ll have the ability to quickly find any item you’re searching for, even years after you’ve stored it. More importantly, using Brisk-Find helps you save considerable space without losing speedy accessibility to your treasured items.</p>
<p class="abs hero-note">Keeping track of all your paper documents and other belongings&nbsp; has never been easier!</p>
<div class="abs cta">START 30 DAY FREE TRIAL</div>

<!-- why -->
<h2 class="abs section-title" style="top:925px">Why <span>Brisk-Find?</span></h2>
<p class="abs why-item" style="left:681px;top:999px">It is extremely easy to use.</p>
<p class="abs why-item" style="left:274px;top:1049px;width:240px">It Adapts to your stile. Since each catalog can have 1 or more levels of depth (folders and sub-folders), Brisk-Find does not force you to use a specific filing or storage methodology.</p>
<p class="abs why-item" style="left:681px;top:1101px;width:230px">It’s very affordable. Checkout our pricing plans!</p>
<p class="abs why-item" style="left:276px;top:1152px;width:220px">Since it is online, your data is available almost anywhere in the world.</p>
<p class="abs why-item" style="left:681px;top:1204px;width:270px">Data encryption ensures that your&nbsp; information is always private, safe, and secure.</p>

<!-- storage -->
<section class="band storage"></section>
<h2 class="abs section-title" style="top:1297px">Why use a storage management system like <span>Brisk-Find?</span></h2>
<div class="abs illus phone-illus" role="img" aria-label="Illustration of a smartphone opening into drawers, with a man holding a large disc"></div>
<h3 class="abs sub-title" style="left:539px;top:1378px">Managing paper documents</h3>
<div class="abs body-copy" style="left:539px;top:1416px;width:475px">
  <p>Most people and businesses have a variety of documents that need to be filed. The problem is how to do it efficiently so that anything you need can easily be found, even well into the future. Normally, you’d put them in folders on file drawers, sorted in some sort of fashion. But which standard is correct for all kinds of documents? There is no set criterion for every kind of document, so you need to use a combination of them.</p>
  <p>As time passes, you might have a difficult time recalling what criterion you used to file your documents, making it hard to find that document with ease. You might not even find it at all. It becomes even more complex when the person doing the searching isn’t the same one as who filed it years ago.</p>
  <p>It is estimated that workers spend over 20% of their time managing documents. A storage management system like Brisk-Find allows any authorized user to instantly find any document regardless of who filed it or which criterion was used, as long as it was properly filed using the system.</p>
</div>

<h3 class="abs sub-title" style="left:0;top:1846px;width:1200px;text-align:center">Managing any non-document objects</h3>
<p class="abs body-copy" style="left:0;top:1880px;width:1200px;text-align:center">The same is true of storing any other kind of objects. Common examples include:</p>

<div class="abs big-phone" role="img" aria-label="Illustration of a large smartphone with open folders holding books, a bottle, a disc and test samples"></div>

<div class="abs left-item" style="left:161px;top:2097px">
  <p class="item-label">Storage boxes, closets,<br>warehouses,and shelves</p>
  <p class="item-text" style="margin-top:6px">Items in storage would better be indexed with a system that lets you find what you’re looking for instantly. Otherwise, you are better off getting rid of those items. In addition to helping you find any object quickly and easily, proper use of Brisk-Find could help you save lots of space!</p>
</div>
<div class="abs left-item" style="left:161px;top:2257px">
  <p class="item-label">Books</p>
  <p class="item-text" style="margin-top:6px">Whether you keep your books on display on shelves, or stored in boxes, you should keep them indexed if you ever want to find any of them in the future.</p>
</div>
<div class="abs left-item" style="left:161px;top:2352px">
  <p class="item-label">Wines</p>
  <p class="item-text" style="margin-top:6px">Maintaining a constant temperature is essential for good care of quality wines. If you are a wine enthusiast, and have even a small wine cellar fridge, keeping your wines indexed on our system would prove invaluable in selecting and locating a wine bottle for any moment without opening that cellar fridge door for too long.</p>
</div>
<div class="abs left-item" style="left:161px;top:2509px">
  <p class="item-label">Safety boxes</p>
  <p class="item-text" style="margin-top:6px">It is common for people to forget exactly which valuables they have stored in their safety boxes or bank safety deposit boxes.</p>
</div>

<div class="abs right-item" style="left:834px;top:2034px">
  <p class="item-label">Moving boxes</p>
  <p class="item-text" style="margin-top:6px">It is always a good idea to record in detail the contents of each box when you move. Since Brisk-Find works well on any modern smartphone, it is easy to record each item as you pack it. After the move, the system makes it easy for you to check that everything that you packed arrived as it should. In addition, if you leave some boxes unopened for a long time, you will always be able to locate the items inside in no time.</p>
</div>
<div class="abs right-item" style="left:834px;top:2208px">
  <p class="item-label">Test samples</p>
  <p class="item-text" style="margin-top:6px">Laboratory samples frequently need to be stored at constant cold temperatures. Our system was originally designed to fulfill the needs of a laboratory which needs an efficient way to minimize the time that the door of their specialized freezers is open while searching for a sample. For confidentiality reasons, each vial was only identified with a code and all the details of the sample and patient would be recorded on our secure system.</p>
</div>
<div class="abs right-item" style="left:834px;top:2383px">
  <p class="item-label">Audio, video, data, and removable<br>media</p>
  <p class="item-text" style="margin-top:6px">Keeping track of the content and storage location of removable media can be a hassle. A system like ours can really help to make that task a breeze.</p>
</div>
<div class="abs right-item" style="left:834px;top:2494px">
  <p class="item-label">Keys</p>
  <p class="item-text" style="margin-top:6px">In a situation such a property management, you can keep track of hundreds of keys for every property you manage. Using Brisk-Find will easily organize your key boxes without losing track of where the keys for each property are located.</p>
</div>

<!-- alternative -->
<h2 class="abs section-title" style="left:0;top:2822px;width:678px;text-align:right">Alternative uses for <span>Brisk-Find</span></h2>
<p class="abs alt-copy">How many times have you gone to a restaurant and couldn’t recall how good (or bad) each of the dishes were that you previously ordered? You can use Brisk-Find to record each one to improve your experience for every visit. Our app can also help you decide where you want to go or which dish to recommend when you have a special occasion.</p>
<div class="abs illus alt-illus" role="img" aria-label="Illustration of a smartphone with drawers and a man holding an orange wine bottle"></div>

<!-- testimonials -->
<section class="band testi"></section>
<h2 class="abs section-title" style="top:3104px">Clients <span>Testomonials</span></h2>
<div class="abs card" style="left:149px">
  <svg class="quote-mark" viewBox="0 0 96 70" aria-hidden="true"><path d="M4 70V40C4 18 14 6 36 2v12C24 18 20 26 20 34h16v36zM56 70V40C56 18 66 6 88 2v12C76 18 72 26 72 34h16v36z" fill="#cfe3f1"/></svg>
  <p class="card-name">Nora K. Vale</p>
  <p class="card-text">Brisk Find made our archive easy to search. We located boxes from years ago in seconds, and the whole office now files things the same way without any extra training.</p>
</div>
<div class="abs card" style="left:625px">
  <svg class="quote-mark" viewBox="0 0 96 70" aria-hidden="true"><path d="M4 70V40C4 18 14 6 36 2v12C24 18 20 26 20 34h16v36zM56 70V40C56 18 66 6 88 2v12C76 18 72 26 72 34h16v36z" fill="#cfe3f1"/></svg>
  <p class="card-name">Edith M. Corran</p>
  <p class="card-text">I track samples, keys and storage boxes in one place. The app is quick on my phone, and finding an old record no longer takes an afternoon of digging.</p>
</div>
<div class="abs avatar" style="left:327px" role="img" aria-label="Client portrait photo"></div>
<div class="abs avatar" style="left:803px" role="img" aria-label="Client portrait photo"></div>
<span class="abs dot" style="left:550px"></span>
<span class="abs dot" style="left:572px"></span>
<span class="abs dot active" style="left:592px"></span>
<span class="abs dot" style="left:616px"></span>
<span class="abs dot" style="left:638px"></span>

<!-- footer -->
<footer class="band footer"></footer>
<h3 class="abs foot-title" style="left:150px;top:3465px">About Us</h3>
<p class="abs foot-text" style="left:150px;top:3500px;width:205px">We build simple tools that help homes and businesses keep track of papers and belongings. Our goal is to make every stored item easy to find, wherever it sits, with a fast search that works on any device.</p>

<h3 class="abs foot-title" style="left:431px;top:3465px">Quick Links</h3>
<div class="abs foot-links" style="left:434px;top:3511px"><a href="#">About</a><a href="#">Pricing</a><a href="#">Blog</a><a href="#">FAQs</a></div>
<div class="abs foot-links" style="left:504px;top:3508px"><a href="#">Suppor</a><a href="#">Reviews</a><a href="#">Contact Us</a><a href="#">Free-Trail</a></div>

<h3 class="abs foot-title" style="left:645px;top:3465px">Contact</h3>
<svg class="abs" style="left:646px;top:3502px" width="18" height="18" viewBox="0 0 24 24" aria-hidden="true"><path d="M6.6 10.8a15 15 0 0 0 6.6 6.6l2.2-2.2c.3-.3.7-.4 1-.2 1.1.4 2.3.6 3.6.6.6 0 1 .4 1 1V20c0 .6-.4 1-1 1A17 17 0 0 1 3 4c0-.6.4-1 1-1h3.5c.6 0 1 .4 1 1 0 1.3.2 2.5.6 3.6.1.3 0 .7-.2 1z" fill="#fff"/></svg>
<p class="abs foot-text" style="left:675px;top:3504px">(555)-010-4321</p>
<svg class="abs" style="left:646px;top:3538px" width="20" height="14" viewBox="0 0 20 14" aria-hidden="true"><rect width="20" height="14" rx="1" fill="#fff"/><path d="M1 1l9 7 9-7" fill="none" stroke="#ef6238" stroke-width="1.6"/></svg>
<p class="abs foot-text" style="left:675px;top:3537px">info@brisk-find.example</p>

<h3 class="abs foot-title" style="left:840px;top:3465px">Location</h3>
<p class="abs foot-text" style="left:841px;top:3508px;width:175px">Suite 12, Harbor Lane, Maple District. Open Monday to Friday, nine to five. Visits by appointment, please call ahead before you come.</p>

<h3 class="abs foot-title" style="left:842px;top:3619px">Keep Connected</h3>
<span class="abs social" style="left:842px;top:3652px"></span>
<span class="abs social" style="left:888px;top:3652px"></span>
<span class="abs social" style="left:842px;top:3693px"></span>
<span class="abs social" style="left:888px;top:3693px"></span>

<div class="band footer-bar">© All Rights are reserved</div>

<!-- lines: timeline and connectors -->
<svg class="abs" style="left:0;top:0;pointer-events:none" width="1200" height="3750" aria-hidden="true">
  <g stroke="#f0643c" stroke-width="1.5">
    <line x1="592" y1="958" x2="592" y2="1270"/>
    <line x1="592" y1="1006" x2="670" y2="1006"/>
    <line x1="515" y1="1057" x2="592" y2="1057"/>
    <line x1="592" y1="1108" x2="670" y2="1108"/>
    <line x1="515" y1="1160" x2="592" y2="1160"/>
    <line x1="592" y1="1211" x2="670" y2="1211"/>
  </g>
  <g fill="#f0643c">
    <circle cx="592" cy="958" r="2"/>
    <circle cx="592" cy="1006" r="7"/><circle cx="670" cy="1006" r="2.5"/>
    <circle cx="592" cy="1057" r="7"/><circle cx="515" cy="1057" r="2.5"/>
    <circle cx="592" cy="1108" r="7"/><circle cx="670" cy="1108" r="2.5"/>
    <circle cx="592" cy="1160" r="7"/><circle cx="515" cy="1160" r="2.5"/>
    <circle cx="592" cy="1211" r="7"/><circle cx="670" cy="1211" r="2.5"/>
  </g>
  <g stroke="#1a5fa6" stroke-width="1.4">
    <line x1="437" y1="2167" x2="437" y2="2577"/>
    <line x1="373" y1="2123" x2="437" y2="2167"/>
    <line x1="374" y1="2271" x2="437" y2="2324"/>
    <line x1="374" y1="2366" x2="437" y2="2417"/>
    <line x1="374" y1="2523" x2="437" y2="2576"/>
    <line x1="760" y1="1969" x2="760" y2="2500"/>
    <line x1="760" y1="1969" x2="826" y2="2028"/>
    <line x1="760" y1="2149" x2="826" y2="2206"/>
    <line x1="760" y1="2324" x2="826" y2="2382"/>
    <line x1="760" y1="2439" x2="826" y2="2494"/>
  </g>
  <g fill="#f0643c">
    <circle cx="437" cy="2167" r="2.5"/><circle cx="437" cy="2324" r="2.5"/>
    <circle cx="437" cy="2417" r="2.5"/><circle cx="437" cy="2576" r="2.5"/>
    <circle cx="760" cy="1969" r="2.5"/><circle cx="760" cy="2149" r="2.5"/>
    <circle cx="760" cy="2324" r="2.5"/><circle cx="760" cy="2439" r="2.5"/>
  </g>
</svg>

</body>
</html>
```